Redesign of business card for Cedar Ridge Mechanical

We are looking for a new design for our business cards for Cedar Ridge Mechanical. We are a plumbing & HVAC construction company, operating on the West Coast of Canada and USA. Logo attached.
Industry/Entity Type
Construction - Plumbing & HVAC
Contact Information for Business Card
Name, address, phone numbers, email, website address
Look and feel
Each slider illustrates characteristics of the customer's brand and the style your logo design should communicate.

```html
<!DOCTYPE html>
<html lang="en">
<head>
<meta charset="UTF-8">
<title>Cedar Ridge Mechanical – Business Card</title>
<link href="https://fonts.googleapis.com/css2?family=Poppins:wght@300;400;700&family=Oswald:wght@500&display=swap" rel="stylesheet">
<style>
  :root {
    --page: #2a2a2c;
    --card: #222326;
    --frame: #ffffff;
    --ink: #ffffff;
    --deep: #151517;
  }
  * { margin: 0; padding: 0; box-sizing: border-box; }
  html, body { width: 1200px; height: 711px; overflow: hidden; background: var(--page); }
  .stage {
    position: relative; width: 1200px; height: 711px;
    display: flex; align-items: center; justify-content: center; gap: 40px;
  }
  .card {
    position: relative; width: 540px; height: 320px;
    background: var(--frame); border-radius: 24px; padding: 12px;
    box-shadow: 0 10px 24px rgba(0,0,0,.45);
  }
  .card-face {
    position: relative; width: 100%; height: 100%;
    background: var(--card); border-radius: 14px; overflow: hidden;
  }
  .notch {
    position: absolute; width: 5px; height: 12px; background: var(--card);
  }
  .notch.top { top: 0; }
  .notch.bottom { bottom: 0; }
  .notch.left { left: 52px; }
  .notch.right { right: 52px; }

  /* Front */
  .front-name {
    position: absolute; inset: 0; display: flex; align-items: center; justify-content: center;
    gap: 14px;
    font-family: 'Poppins', sans-serif; font-weight: 700; font-size: 30px;
    color: var(--deep); letter-spacing: .5px;
  }
  .front-name .mark { width: 26px; height: 26px; background: var(--deep); }

  /* Back */
  .brand {
    position: absolute; top: 30px; right: 30px; display: flex; align-items: center; gap: 10px;
    font-family: 'Poppins', sans-serif; font-weight: 400; font-size: 19px; color: var(--ink);
  }
  .brand .mark { width: 18px; height: 18px; border: 3px solid var(--ink); }
  .contact {
    position: absolute; left: 30px; bottom: 26px;
    font-family: 'Poppins', sans-serif; color: var(--ink);
  }
  .person { font-size: 26px; line-height: 1.05; }
  .person .given { font-weight: 700; }
  .person .family { font-weight: 300; }
  .role { font-size: 13px; font-weight: 400; margin-top: 2px; }
  .address { font-size: 13px; font-weight: 300; margin-top: 10px; line-height: 1.35; }
  .links { list-style: none; margin-top: 10px; font-size: 13px; font-weight: 300; line-height: 1.55; }
  .links li { display: flex; align-items: center; gap: 8px; }
  .links svg { width: 12px; height: 12px; fill: none; stroke: var(--ink); stroke-width: 2; }
</style>
</head>
<body>
<main class="stage">
  <section class="card card-front">
    <div class="card-face">
      <div class="front-name"><span class="mark"></span>Cedar Ridge Mechanical</div>
    </div>
    <span class="notch top left"></span><span class="notch top right"></span>
    <span class="notch bottom left"></span><span class="notch bottom right"></span>
  </section>

  <section class="card card-back">
    <div class="card-face">
      <div class="brand"><span class="mark"></span>Cedar Ridge Mechanical</div>
      <div class="contact">
        <p class="person"><span class="given">Marta</span> <span class="family">Kovalenko</span></p>
        <p class="role">Founder &amp; CEO</p>
        <p class="address">418 Harbor Ln. Suite 310<br>Bellingham, WA 98225</p>
        <ul class="links">
          <li><svg viewBox="0 0 24 24"><path d="M5 3h4l2 5-3 2a11 11 0 0 0 6 6l2-3 5 2v4a2 2 0 0 1-2 2A17 17 0 0 1 3 5a2 2 0 0 1 2-2z"/></svg>(360) 555-0142</li>
          <li><svg viewBox="0 0 24 24"><circle cx="12" cy="12" r="9"/><path d="M3 12h18M12 3c3 3 3 15 0 18M12 3c-3 3-3 15 0 18"/></svg>info@cedarridgemech.com</li>
          <li><svg viewBox="0 0 24 24"><rect x="3" y="5" width="18" height="14" rx="1"/><path d="M3 6l9 7 9-7"/></svg>www.cedarridgemech.com</li>
        </ul>
      </div>
    </div>
    <span class="notch top left"></span><span class="notch top right"></span>
    <span class="notch bottom left"></span><span class="notch bottom right"></span>
  </section>
</main>
</body>
</html>
```